Website for Ashcombe Tube Drift

Require a website for a river float in the City of Edmonton. Located on North Saskatchewan River. Will need to be a coded website with incorporated booking system through Fare Harbor software.

Pages include
Home
Pricing
About
FAQ
Contact

Ashcombe Tube Drift is an activity based business that will have customers floating down the North Saskatchewan river in Edmonton AB. The site will have all information needed and a full reservation system. The project was launched to provide people in the Edmonton area a favorite summer activity.

Here are similar websites to reference what our business will be doing and what we are looking for.

mossbankfloatco.com
quillpointpaddles.com

Target Market(s)

Families, Groups, Individuals, Anyone who wants to explore the river

Industry/Entity Type

Activities based business/ Outdoor recreational/ River Float

Coding

Coded - Design and coding required

Number of Pages Required

5+ page

Colors
0054AA
0677BA
7BADD7
CADEEF
E8F1F8
F0912C
F2A743
F7CA91
FBE8D2
FDF5EE

```html
<!DOCTYPE html>
<html lang="en">
<head>
<meta charset="utf-8">
<title>Ashcombe Tube Drift</title>
<link href="https://fonts.googleapis.com/css2?family=Ubuntu:wght@400;500;700&display=swap" rel="stylesheet">
<style>
:root{
  --navy:#0a2d6e;
  --orange:#e0582a;
  --orange-soft:#d95c30;
  --sky:#4fc3e8;
  --hero-top:#2d4f86;
  --hero-bottom:#3d5f8f;
  --faq-top:#245a94;
  --faq-bottom:#4f8fb0;
  --photo:#6f96b8;
  --ink:#1b1b1b;
  --white:#ffffff;
  --black:#000000;
}
*{box-sizing:border-box;margin:0;padding:0}
html,body{width:1200px;height:3497px;overflow:hidden}
body{position:relative;font-family:"Ubuntu",sans-serif;color:var(--ink);background:var(--white)}
.abs{position:absolute}
a{color:inherit;text-decoration:none}

/* top bar */
.topbar{left:0;top:0;width:1200px;height:76px;background:var(--navy)}
.topbar .phone{left:110px;top:22px;color:var(--white);font-size:17px;font-weight:500;display:flex;align-items:center;gap:12px}
.ring{width:32px;height:32px;border:2px solid var(--white);border-radius:50%;display:flex;align-items:center;justify-content:center}
.socials{display:flex;gap:22px}
.topbar .socials{right:110px;top:20px}
.social-dot{width:34px;height:34px;border:2px solid var(--white);border-radius:50%}

/* nav */
.nav{left:0;top:76px;width:1200px;height:81px;background:var(--white)}
.nav a{position:absolute;top:29px;font-size:19px;font-weight:500;color:var(--ink)}
.brand-badge{left:521px;top:43px;width:158px;height:158px;border-radius:50%;background:var(--white);display:flex;flex-direction:column;align-items:center;justify-content:center;z-index:5}
.brand-badge .mark{width:52px;height:52px;border-radius:50%;background:var(--sky);margin-bottom:8px}
.brand-badge .name{font-size:15px;font-weight:700;color:var(--navy);text-align:center;line-height:1.15}

/* hero */
.hero{left:0;top:157px;width:1200px;height:672px;background:linear-gradient(180deg,var(--hero-top) 0%,var(--hero-bottom) 100%)}
.hero h1{position:absolute;left:0;top:118px;width:1200px;text-align:center;color:var(--white);font-size:64px;font-weight:700;line-height:1.07;letter-spacing:1px}
.btn{display:flex;align-items:center;justify-content:center;border-radius:34px;color:var(--white);font-weight:500;font-size:22px}
.btn-navy{background:var(--navy);box-shadow:0 4px 8px rgba(0,0,0,.25)}
.btn-orange{background:var(--orange)}
.hero .book{left:497px;top:278px;width:175px;height:64px}
.hero-wave{left:0;top:600px;width:1200px;height:230px;z-index:2}

/* section titles */
.title{font-size:30px;font-weight:500;color:var(--ink);display:inline-flex;position:absolute}
.bubbles{position:absolute;width:24px;height:24px}

/* about */
.about-title{left:113px;top:882px}
.about-text{left:112px;top:932px;width:480px;font-size:15px;line-height:26px;font-weight:500;color:#222}
.about-text p+p{margin-top:26px}
.about .read{left:113px;top:1158px;width:175px;height:64px}
.about-art{left:640px;top:862px;width:446px;height:330px;border-radius:50%;background:var(--sky)}

/* faq */
.faq{left:0;top:1312px;width:1200px;height:853px;background:linear-gradient(180deg,var(--faq-top) 0%,var(--faq-bottom) 100%)}
.faq .title{color:var(--white);left:393px;top:86px;font-weight:700}
.faq-item{position:absolute;left:109px;width:977px;border:2px solid rgba(255,255,255,.9);border-radius:34px;color:var(--white)}
.faq-item .q{position:absolute;left:30px;top:0;height:100%;display:flex;align-items:center;gap:12px;font-size:20px}
.toggle{position:absolute;right:28px;width:42px;height:40px;background:var(--navy);border-radius:3px;display:flex;align-items:center;justify-content:center}
.faq-open{position:absolute;left:109px;top:1565px;width:977px;height:210px;background:var(--orange-soft);border-radius:30px;color:var(--white);box-shadow:0 6px 10px rgba(0,0,0,.2)}
.faq-open .q{position:absolute;left:28px;top:0;height:72px;display:flex;align-items:center;gap:12px;font-size:20px}
.faq-open .rule{position:absolute;left:0;top:72px;width:100%;height:1px;background:rgba(255,255,255,.45)}
.faq-open .toggle{top:15px;background:var(--white)}
.faq-open .a{position:absolute;left:28px;top:90px;width:925px;font-size:14.5px;line-height:26px}

/* pricing */
.price-photo{left:110px;top:2220px;width:474px;height:338px;border-radius:237px 237px 0 0;border:12px solid var(--navy);border-bottom:none;background:var(--photo)}
.price-title{left:641px;top:2238px}
.price-sub{left:641px;top:2290px;font-size:20px;font-weight:500;display:flex;align-items:baseline;gap:8px}
.price-sub small{font-size:14px;color:var(--orange)}
.price-text{left:641px;top:2328px;width:470px;font-size:15px;line-height:26px;font-weight:500;color:#222}
.feature{position:absolute;display:flex;align-items:center;gap:10px;font-size:15px;font-weight:500}
.price-note{left:641px;top:2488px;font-size:15px;font-weight:500;color:#222}
.price-btn{left:642px;top:2527px;width:175px;height:64px}

/* mailing */
.mailing{left:0;top:2664px;width:1200px;height:460px;background:var(--sky)}
.mailing .title{color:var(--white);left:405px;top:72px;font-weight:700}
.signup{left:243px;top:142px;width:715px;height:68px;border-radius:34px;background:var(--white);overflow:hidden}
.signup .field{position:absolute;left:40px;top:24px;font-size:15px;font-weight:500;color:#333}
.signup .sub{position:absolute;right:0;top:0;width:202px;height:68px;background:var(--navy);border-radius:34px 34px 34px 0;color:var(--white);font-size:25px;font-weight:500;display:flex;align-items:center;justify-content:center}
.foot-wave{left:0;top:2930px;width:1200px;height:200px}

/* footer */
.footer{left:0;top:3125px;width:1200px;height:372px;background:var(--black);color:var(--white)}
.foot-brand{position:absolute;left:110px;top:20px;width:270px;display:flex;flex-direction:column;align-items:center}
.foot-brand .mark{width:150px;height:150px;border-radius:50%;background:var(--sky);margin-bottom:12px}
.foot-brand .name{font-size:28px;font-weight:700;color:var(--sky);text-align:center;line-height:1.05}
.foot-col{position:absolute;top:28px}
.foot-col h4{font-size:20px;font-weight:500;margin-bottom:20px;letter-spacing:.5px}
.foot-col li{list-style:none;font-size:15px;height:41px;display:flex;align-items:flex-start;gap:8px}
.contact-row{display:flex;gap:14px;font-size:15px;line-height:20px;margin-bottom:22px}
.foot-rule{position:absolute;left:110px;top:281px;width:977px;height:1px;background:rgba(255,255,255,.6)}
.foot-legal{position:absolute;left:110px;top:313px;font-size:14px}
.footer .socials{position:absolute;right:113px;top:303px}
</style>
</head>
<body>

<header class="abs topbar">
  <div class="abs phone">
    <span class="ring"><svg width="16" height="16" viewBox="0 0 24 24" fill="none" stroke="#fff" stroke-width="2"><path d="M5 3h4l2 5-3 2a12 12 0 0 0 6 6l2-3 5 2v4a2 2 0 0 1-2 2A17 17 0 0 1 3 5a2 2 0 0 1 2-2z"/></svg></span>
    Phone No: +1 780 555 0142
  </div>
  <div class="abs socials" aria-label="Social links">
    <span class="social-dot"></span><span class="social-dot"></span><span class="social-dot"></span><span class="social-dot"></span>
  </div>
</header>

<nav class="abs nav">
  <a style="left:109px">Home</a>
  <a style="left:236px">About</a>
  <a style="left:364px">Services</a>
  <a style="left:741px">Pricing</a>
  <a style="left:879px">FAQ</a>
  <a style="left:989px">Contact us</a>
</nav>
<div class="abs brand-badge">
  <span class="mark"></span>
  <span class="name">Ashcombe<br>Tube Drift</span>
</div>

<section class="abs hero" role="img" aria-label="Hero photo of the city skyline above the river valley">
  <h1>Welcome To<br>Ashcombe Tube Drift</h1>
  <a class="abs btn btn-navy book">Book Now</a>
</section>
<svg class="abs hero-wave" viewBox="0 0 1200 230" preserveAspectRatio="none">
  <path fill="#e0582a" d="M0 118 C120 132 260 180 400 182 C540 184 600 90 740 48 C860 14 960 22 1060 58 C1120 80 1170 80 1200 66 L1200 138 C1150 150 1100 120 1040 106 C960 88 860 104 780 130 C690 160 640 222 540 226 C420 230 340 190 260 172 C170 150 80 176 0 156 Z"/>
  <path fill="#fff" d="M0 156 C80 176 170 150 260 172 C340 190 420 230 540 226 C640 222 690 160 780 130 C860 104 960 88 1040 106 C1100 120 1150 150 1200 138 L1200 230 L0 230 Z"/>
</svg>

<section class="about">
  <h2 class="title about-title">About Ashcombe Tube Drift
    <svg class="bubbles" style="right:-28px;top:-20px" viewBox="0 0 24 24"><circle cx="8" cy="8" r="5" fill="none" stroke="#4fc3e8" stroke-width="3"/><circle cx="19" cy="17" r="3" fill="none" stroke="#4fc3e8" stroke-width="2"/></svg>
  </h2>
  <div class="abs about-text">
    <p>Float the North Saskatchewan through downtown Edmonton. Edmonton's Best Summer Activity We provide the lifejacket, paddle, river tube and shuttle service.</p>
    <p>You just have to show up. Ashcombe Tube Drift was launched to provide people in the Edmonton area a favorite summer activity. Nothing is better on a hot summer day, than spending it on the river and seeing Edmonton from a new perspective.</p>
  </div>
  <a class="abs btn btn-navy read">Read More</a>
  <div class="abs about-art" role="img" aria-label="Illustration of a river tube floating beneath a bridge"></div>
</section>

<section class="abs faq" role="img" aria-label="Background photo of riverside greenery">
  <h2 class="title">Frequently Asked Questions
    <svg class="bubbles" style="right:-30px;top:-18px" viewBox="0 0 24 24"><circle cx="8" cy="8" r="5" fill="none" stroke="#fff" stroke-width="3"/><circle cx="19" cy="17" r="3" fill="none" stroke="#fff" stroke-width="2"/></svg>
  </h2>
</section>

<div class="faq-item" style="top:1479px;height:68px">
  <div class="q"><svg width="22" height="16" viewBox="0 0 22 16" fill="none" stroke="#fff" stroke-width="2"><path d="M1 8h19M13 1l7 7-7 7"/></svg>How do I reserve my float?</div>
  <span class="toggle" style="top:13px"><svg width="16" height="16" viewBox="0 0 16 16"><path d="M8 1v14M1 8h14" stroke="#fff" stroke-width="3"/></svg></span>
</div>
<div class="faq-open">
  <div class="q"><svg width="22" height="16" viewBox="0 0 22 16" fill="none" stroke="#fff" stroke-width="2"><path d="M1 8h19M13 1l7 7-7 7"/></svg>What safety information should I know?</div>
  <span class="toggle"><svg width="18" height="4" viewBox="0 0 18 4"><path d="M0 2h18" stroke="#e0582a" stroke-width="2.5"/></svg></span>
  <div class="rule"></div>
  <p class="a">Children 12 years and younger should be accompanied by an adult at all times on the river. Life jackets and paddles are provided and are recommended for everyone, especially if you are a weak or inexperienced swimmer. You must exit the river at the designated exit point (rafters landing) and are responsible for doing so. There are no lifeguards on site, and all floaters enter and exit the river at their own risk. Staff safety demonstration is provided before entering the river.</p>
</div>
<div class="faq-item" style="top:1793px;height:68px">
  <div class="q"><svg width="22" height="16" viewBox="0 0 22 16" fill="none" stroke="#fff" stroke-width="2"><path d="M1 8h19M13 1l7 7-7 7"/></svg>What is included?</div>
  <span class="toggle" style="top:13px"><svg width="16" height="16" viewBox="0 0 16 16"><path d="M8 1v14M1 8h14" stroke="#fff" stroke-width="3"/></svg></span>
</div>
<div class="faq-item" style="top:1878px;height:68px">
  <div class="q"><svg width="22" height="16" viewBox="0 0 22 16" fill="none" stroke="#fff" stroke-width="2"><path d="M1 8h19M13 1l7 7-7 7"/></svg>What should I bring?</div>
  <span class="toggle" style="top:13px"><svg width="16" height="16" viewBox="0 0 16 16"><path d="M8 1v14M1 8h14" stroke="#fff" stroke-width="3"/></svg></span>
</div>
<a class="abs btn btn-orange" style="left:512px;top:2019px;width:175px;height:64px">View More</a>

<section class="pricing">
  <div class="abs price-photo" role="img" aria-label="Photo of river tubes on the water by a wooded shore"></div>
  <h2 class="title price-title">Our Pricing
    <svg class="bubbles" style="right:-28px;top:-18px" viewBox="0 0 24 24"><circle cx="8" cy="8" r="5" fill="none" stroke="#4fc3e8" stroke-width="3"/><circle cx="19" cy="17" r="3" fill="none" stroke="#4fc3e8" stroke-width="2"/></svg>
  </h2>
  <div class="abs price-sub">Tube and Shuttle <small>(Price: $30/person)</small></div>
  <p class="abs price-text">We keep our pricing simple and include everything you need: Premium comfort float tube with backrest and cup holder</p>
  <div class="feature" style="left:641px;top:2388px"><svg width="20" height="14" viewBox="0 0 22 16" fill="none" stroke="#111" stroke-width="2.4"><path d="M1 8h19M13 1l7 7-7 7"/></svg>Lifejacket</div>
  <div class="feature" style="left:803px;top:2388px"><svg width="20" height="14" viewBox="0 0 22 16" fill="none" stroke="#111" stroke-width="2.4"><path d="M1 8h19M13 1l7 7-7 7"/></svg>Safety training</div>
  <div class="feature" style="left:641px;top:2422px"><svg width="20" height="14" viewBox="0 0 22 16" fill="none" stroke="#111" stroke-width="2.4"><path d="M1 8h19M13 1l7 7-7 7"/></svg>Paddle</div>
  <div class="feature" style="left:803px;top:2422px"><svg width="20" height="14" viewBox="0 0 22 16" fill="none" stroke="#111" stroke-width="2.4"><path d="M1 8h19M13 1l7 7-7 7"/></svg>Staff assistance</div>
  <div class="feature" style="left:641px;top:2454px"><svg width="20" height="14" viewBox="0 0 22 16" fill="none" stroke="#111" stroke-width="2.4"><path d="M1 8h19M13 1l7 7-7 7"/></svg>Parking</div>
  <div class="feature" style="left:803px;top:2454px"><svg width="20" height="14" viewBox="0 0 22 16" fill="none" stroke="#111" stroke-width="2.4"><path d="M1 8h19M13 1l7 7-7 7"/></svg>Round trip shuttle service</div>
  <p class="abs price-note">Group of 10 or more? (Does not include taxes or fees)</p>
  <a class="abs btn btn-navy price-btn">Contact Us</a>
</section>

<section class="abs mailing" role="img" aria-label="Faded background photo of the city skyline">
  <h2 class="title">Signup for our Mailing List
    <svg class="bubbles" style="right:-28px;top:-18px" viewBox="0 0 24 24"><circle cx="8" cy="8" r="5" fill="none" stroke="#fff" stroke-width="3"/><circle cx="19" cy="17" r="3" fill="none" stroke="#fff" stroke-width="2"/></svg>
  </h2>
  <div class="abs signup">
    <span class="field">Enter Your Email</span>
    <span class="sub">Subscribe</span>
  </div>
</section>
<svg class="abs foot-wave" viewBox="0 0 1200 200" preserveAspectRatio="none">
  <path fill="#e0582a" d="M0 100 C60 70 110 110 180 90 C260 60 330 60 400 30 C460 5 520 40 580 48 C660 58 700 110 790 100 C880 90 920 150 1010 110 C1080 80 1120 30 1200 20 L1200 70 C1140 80 1100 150 1020 160 C930 170 880 130 800 140 C720 150 680 110 600 96 C530 84 480 60 420 80 C350 104 300 110 230 120 C160 130 90 170 0 180 Z"/>
  <path fill="#000" d="M0 180 C90 170 160 130 230 120 C300 110 350 104 420 80 C480 60 530 84 600 96 C680 110 720 150 800 140 C880 130 930 170 1020 160 C1100 150 1140 80 1200 70 L1200 200 L0 200 Z"/>
</svg>

<footer class="abs footer">
  <div class="foot-brand">
    <span class="mark"></span>
    <span class="name">Ashcombe<br>Tube Drift</span>
  </div>
  <div class="foot-col" style="left:445px">
    <h4>QUICK LINKS</h4>
    <ul><li>» Home</li><li>» About us</li><li>» Our Pricing</li><li>» Contact us</li></ul>
  </div>
  <div class="foot-col" style="left:639px">
    <h4>HELP CENTER</h4>
    <ul><li>» Privacy</li><li>» Terms</li><li>» FAQ</li><li>» Policy</li></ul>
  </div>
  <div class="foot-col" style="left:839px">
    <h4>CONTACT US</h4>
    <div class="contact-row"><svg width="16" height="18" viewBox="0 0 16 20" fill="none" stroke="#fff" stroke-width="1.6"><path d="M8 19s6-6 6-11A6 6 0 0 0 2 8c0 5 6 11 6 11z"/><circle cx="8" cy="8" r="2.2"/></svg><span>4127 Riverbend Rd NW,<br>Edmonton, AB</span></div>
    <div class="contact-row"><svg width="16" height="16" viewBox="0 0 24 24" fill="none" stroke="#fff" stroke-width="2"><path d="M5 3h4l2 5-3 2a12 12 0 0 0 6 6l2-3 5 2v4a2 2 0 0 1-2 2A17 17 0 0 1 3 5a2 2 0 0 1 2-2z"/></svg><span>+1 780 555 0142</span></div>
    <div class="contact-row" style="margin-top:26px"><svg width="16" height="14" viewBox="0 0 20 14" fill="none" stroke="#fff" stroke-width="1.6"><rect x="1" y="1" width="18" height="12"/><path d="M1 1l9 7 9-7"/></svg><span>hello@ashcombetubedrift.com</span></div>
  </div>
  <div class="foot-rule"></div>
  <p class="foot-legal">Copyrights@2022.ashcombetubedrift.com &nbsp;&nbsp; | &nbsp;&nbsp; All Rights Reserved</p>
  <div class="socials" aria-label="Social links">
    <span class="social-dot"></span><span class="social-dot"></span><span class="social-dot"></span><span class="social-dot"></span>
  </div>
</footer>

</body>
</html>
```